Cutting Edge Property Services Provider is Looking to Update Business Card Design

We are looking to freshen up our business cards to match our cutting edge technology based image.

KORVANEX - Where Care Finds Its Pulse

More information about our company can be found on our website at www.korvanex-demo.net

We integrate technology in a historically low tech industry.

We have appeared on the Brisk 300/3000 list 2 years in a row and we're previously recognized as the 5th Quickest Rising Firm in San Diego.

Our core colors are blue and white, but are not against accents that might improve our image.

We currently have our Mission Statement on our Business Cards in a folding design:
KORVANEX IS THE LEADING BUILDING SERVICES INNOVATOR. BY COMBINING TECHNOLOGY WITH FUNCTIONAL TOOS THAT IMPROVE EFFICIENCY IN THE WORKPLACE, WE PROVIDE UNPARALLELED SERVICE IN THE INDUSTRY. DEVELOPING LASTING RELATIONSHIPS WITH OUR CLIENTS AND ASSOCIATES IS THE CORNERSTONE OF OUR SUCCESS.

We'd like to convey the image of a cutting edge, technology based company. Want the cards to pop.

Target Market(s)

Commercial Property Managers - 20 to 50 year old professionals

Industry/Entity Type

Business

Requirements
Must have
• Must utilize our logo obviously, but are definitely open to using variations on the logo. Utilizing the components of the logo, but maybe in different configurations or backgrounds, etc...

Must use the Name: KORVANEX.
Can also use KORVANEX PROPERTY SERVICES.

Must include the Mission Statement

Must say: Where Care Finds Its Pulse
Nice to have
• We are considering plastic stock, shaped cards, or folding cards.

Nothing over the top or really expensive, but will consider if it conveys innovation and technology.
Should not have
• No images of toilets, buildings, trees, or anything relating to commercial properties.

We want to convey our technology image.

```html
<!DOCTYPE html>
<html lang="en">
<head>
<meta charset="utf-8">
<title>KORVANEX Business Card</title>
<link rel="stylesheet" href="https://fonts.googleapis.com/css2?family=Exo+2:wght@400;700;800&family=PT+Sans&display=swap">
<style>
  :root {
    --brand-blue: #1d5688;
    --deep-blue: #0f4a7e;
    --silver-light: #f3f3f3;
    --silver-mid: #dcdcdc;
    --silver-dark: #b9bcc0;
    --paper-white: #ffffff;
    --backdrop: #e6e4e1;
    --text-white: #ffffff;
  }
  * { margin: 0; padding: 0; box-sizing: border-box; }
  html, body { width: 1200px; height: 716px; overflow: hidden; }
  body { background: var(--backdrop); position: relative; font-family: "Exo 2", sans-serif; }

  .card {
    position: absolute;
    width: 546px;
    height: 311px;
    border-radius: 24px;
    overflow: hidden;
    box-shadow: 0 3px 10px rgba(0,0,0,0.18);
  }
  .card--silver { background: linear-gradient(160deg, var(--silver-light) 0%, #e9e9e9 55%, var(--silver-mid) 100%); }
  .card--white { background: var(--paper-white); }

  .card-front { left: 42px; top: 47px; }
  .card-back-silver { left: 42px; top: 381px; }
  .card-back-white { left: 613px; top: 199px; }

  .front-wave { position: absolute; inset: 0; width: 100%; height: 100%; }

  .holder { position: absolute; right: 26px; top: 24px; text-align: right; color: var(--brand-blue); }
  .holder-name { font-weight: 800; font-size: 18px; letter-spacing: 0.3px; }
  .holder-title { font-weight: 700; font-size: 13px; }

  .brand { position: absolute; left: 44px; top: 128px; color: var(--brand-blue); }
  .brand-name { font-weight: 800; font-size: 30px; letter-spacing: 1px; line-height: 1; }
  .brand-tagline { font-weight: 400; font-size: 13px; margin-top: 4px; }

  .contact { position: absolute; right: 24px; top: 180px; text-align: right; color: var(--text-white); font-size: 14px; line-height: 21px; }
  .contact-line { display: flex; justify-content: flex-end; align-items: center; gap: 5px; }
  .contact-line svg { width: 11px; height: 11px; fill: var(--text-white); }
  .address { margin-top: 13px; font-size: 13.5px; line-height: 20px; }

  .mission {
    position: absolute; left: 0; right: 0; top: 78px;
    text-align: center;
    font-family: "PT Sans", sans-serif;
    font-size: 16px;
    line-height: 30.5px;
    color: var(--brand-blue);
    text-transform: uppercase;
  }
</style>
</head>
<body>

  <section class="card card--silver card-front">
    <svg class="front-wave" viewBox="0 0 546 311" aria-hidden="true">
      <path d="M0,232 C160,268 330,218 546,150 L546,176 C330,236 160,282 0,252 Z" fill="var(--silver-dark)" opacity="0.55"/>
      <path d="M0,262 C150,292 320,246 546,170 L546,311 L0,311 Z" fill="var(--deep-blue)"/>
      <path d="M0,262 C150,292 320,246 546,170" fill="none" stroke="#ffffff" stroke-width="3" opacity="0.7"/>
    </svg>

    <div class="holder">
      <div class="holder-name">Your Name</div>
      <div class="holder-title">Title</div>
    </div>

    <div class="brand">
      <div class="brand-name">KORVANEX</div>
      <div class="brand-tagline">Where Care Finds Its Pulse</div>
    </div>

    <div class="contact">
      <div class="contact-line">
        <svg viewBox="0 0 24 24"><path d="M6.6 10.8a15.1 15.1 0 0 0 6.6 6.6l2.2-2.2a1 1 0 0 1 1-.25 11.4 11.4 0 0 0 3.6.57 1 1 0 0 1 1 1V20a1 1 0 0 1-1 1A17 17 0 0 1 3 4a1 1 0 0 1 1-1h3.5a1 1 0 0 1 1 1c0 1.25.2 2.45.57 3.57a1 1 0 0 1-.25 1z"/></svg>
        <span>1(866) 555-0142</span>
      </div>
      <div class="contact-line">
        <svg viewBox="0 0 24 24"><path d="M2 6h20v12H2z M2 6l10 7 10-7" /></svg>
        <span>info@korvanex-demo.net</span>
      </div>
      <div class="contact-line">
        <svg viewBox="0 0 24 24"><circle cx="12" cy="12" r="10"/></svg>
        <span>www.korvanex-demo.net</span>
      </div>
      <div class="address">
        1480 Harbor Crest Ave.<br>
        Suite 210, San Diego, CA 92108
      </div>
    </div>
  </section>

  <section class="card card--silver card-back-silver">
    <p class="mission">
      KORVANEX is the leading building services innovator.<br>
      By combining technology with functional toos that<br>
      improve efficiency in the workplace, we provide<br>
      unparalleled service in the industry. Developing<br>
      lasting relationships with our clients and associates<br>
      is the cornerstone of our success.
    </p>
  </section>

  <section class="card card--white card-back-white">
    <p class="mission">
      KORVANEX is the leading building services innovator.<br>
      By combining technology with functional toos that<br>
      improve efficiency in the workplace, we provide<br>
      unparalleled service in the industry. Developing<br>
      lasting relationships with our clients and associates<br>
      is the cornerstone of our success.
    </p>
  </section>

</body>
</html>
```